Tidy paddock Services

After a high quality design website. we are a company that provides services to people that own land and need a hand getting on top of the delayed jobs.
would want a number of tab/ pages for the web page.
Home page / About us page / services page / Gallery page. / Contact us page
we offer a wide range of services .listed below

Stock Work (title)

Stock movement
Break feeding
Temporary staffing

Spraying (title)

Spraying weeds
Spraying gorse

Pastures (title)

Fertilizing
Topping

Building (title)

Habitable sheds
Farm sheds
Sheep yards
Cattle yards
Repair farm buildings
Decks
Retaining walls

Fencing (title)

Stock fencing
Post & rail
Stock yards repair
Electric fencing install & repairs

Water Management (title)

Water trough installation
Water scheme install
Water trough cleaning
Farm water maintenance
Water ponds
Ornamental ponds
Drainage

General (title)

Lawn mowing
Hedge trimming
Pruning trees
Metaling drive ways & races
Water blasting
Small digger work
Little tip truck cartage
Home kill management
Mulching gorse
Section clearing

```html
<!DOCTYPE html>
<html lang="en">
<head>
<meta charset="utf-8">
<title>Tidy paddock Services</title>
<link href="https://fonts.googleapis.com/css2?family=Montserrat:wght@500;600;700;800&family=Lato:wght@400;700&family=Noto+Serif:wght@500&display=swap" rel="stylesheet">
<style>
:root{
  --green:#5f9a13;
  --green-bright:#6aa817;
  --green-band:#639a1c;
  --ink:#111;
  --text:#333;
  --muted:#666;
  --white:#fff;
  --black:#0b0b0b;
}
*{box-sizing:border-box;margin:0;padding:0}
html,body{width:1200px;height:4721px;overflow:hidden;background:var(--white)}
body{position:relative;font-family:"Lato",sans-serif;color:var(--text)}
.abs{position:absolute}
.brand{display:flex;align-items:center;gap:10px;font-family:"Montserrat",sans-serif;font-weight:700;color:var(--green)}
.brand .dot{width:18px;height:18px;border-radius:50%;background:var(--green)}

/* header */
.topbar{left:330px;top:0;width:870px;height:48px;background:var(--green);clip-path:polygon(0 0,100% 0,100% 100%,40px 100%)}
.topbar .item{position:absolute;top:10px;display:flex;align-items:center;gap:12px;color:#fff;font-size:15px}
.ico-circle{width:28px;height:28px;border-radius:50%;background:#fff;display:flex;align-items:center;justify-content:center}
.social{position:absolute;top:10px;width:28px;height:28px;border-radius:50%;background:#fff}
.nav{top:62px;left:0;width:1200px;height:22px;font-size:16px}
.nav a{position:absolute;color:var(--ink);text-decoration:none}
.nav a.active{color:var(--green)}

/* hero */
.hero{left:0;top:95px;width:1200px;height:610px;background:linear-gradient(90deg,#33402a 0%,#4f6234 35%,#7a8a58 60%,#5e7a3a 80%,#3f5e27 100%)}
.hero h1{position:absolute;left:112px;top:160px;font-family:"Montserrat",sans-serif;font-weight:700;font-size:46px;line-height:60px;color:#fff}
.hero p{position:absolute;left:112px;top:290px;width:440px;font-size:14px;line-height:31px;color:#fff}
.btn{display:inline-flex;align-items:center;justify-content:center;background:var(--green);color:#fff;font-family:"Montserrat",sans-serif;font-weight:700;font-size:15px}
.hero .btn{position:absolute;left:112px;top:365px;width:133px;height:44px}
.arrow-c{position:absolute;width:26px;height:26px;border-radius:50%;border:1.5px solid #fff;display:flex;align-items:center;justify-content:center}

/* headings */
.title{position:absolute;left:0;width:1200px;text-align:center;font-family:"Montserrat",sans-serif;font-weight:700}
.title .l1{font-size:32px;color:var(--ink)}
.title .l1 .g{color:var(--green)}
.title .l2{font-size:32px;color:var(--ink);display:flex;justify-content:center;align-items:center;gap:10px}
.title .l2 i{display:block;width:58px;height:3px;background:var(--ink)}

/* why */
.why-text{left:120px;top:943px;width:960px;text-align:center;font-size:14px;line-height:31px;color:var(--text)}
.feature{position:absolute;top:1040px;width:200px;text-align:center}
.feature svg{display:block;margin:0 auto 18px}
.feature span{font-family:"Noto Serif",serif;font-size:19px;color:var(--ink)}

/* about */
.about{left:0;top:1237px;width:1200px;height:648px;background:var(--green-band)}
.about-photo{left:166px;top:1363px;width:400px;height:400px;border-radius:50%;border:8px solid #fff;background:linear-gradient(180deg,#8fb5d9 0%,#6b8a4a 45%,#9a6a42 75%,#c99868 100%)}
.about h2{position:absolute;left:637px;top:142px;font-family:"Montserrat",sans-serif;font-weight:700;font-size:32px;color:#fff;display:flex;align-items:center;gap:6px}
.about h2 i{display:block;width:52px;height:3px;background:#fff}
.about p{position:absolute;left:608px;top:228px;width:485px;font-size:14.5px;line-height:31px;color:#fff}
.about .btn{position:absolute;left:608px;top:503px;width:132px;height:43px;background:#fff;color:var(--green)}

/* services */
.svc-brand{left:0;top:2012px;width:1200px;justify-content:center;font-size:32px}
.card{position:absolute;top:2140px;width:317px;background:#fff;box-shadow:0 4px 12px rgba(0,0,0,.15);border-bottom:8px solid var(--black);border-radius:6px;overflow:hidden}
.card .pic{height:247px}
.card h3{font-family:"Montserrat",sans-serif;font-weight:700;font-size:17px;text-align:center;padding:30px 0 20px;color:var(--ink)}
.card.featured{border:6px solid var(--green-bright);border-top:none;border-radius:6px}
.card.featured h3{color:var(--green);font-size:21px;padding:22px 0 10px}
.card.featured ul{list-style:none;text-align:center;font-size:14px;line-height:31px;padding-bottom:20px}
.svc-arrow{position:absolute;top:2269px;width:24px;height:24px;border-radius:50%;border:1.5px solid #777;display:flex;align-items:center;justify-content:center}

/* gallery */
.gallery{left:0;top:2726px;width:1200px;height:969px;background:var(--green-band)}
.gallery h2{position:absolute;left:533px;top:125px;font-family:"Montserrat",sans-serif;font-weight:700;font-size:32px;color:#fff;display:flex;align-items:center;gap:6px}
.gallery h2 i{display:block;width:52px;height:3px;background:#fff}
.tile{position:absolute;border:3px solid #fff}

/* contact */
.field{position:absolute;height:46px;background:#fff;box-shadow:0 2px 10px rgba(0,0,0,.14);border-radius:5px;padding:14px 18px;font-size:14px;color:var(--muted)}
.contact-submit{left:531px;top:4170px;width:136px;height:47px}

/* footer */
.footer{left:0;top:4309px;width:1200px;height:412px;background:var(--black);color:#fff}
.footer h4{position:absolute;top:81px;font-family:"Montserrat",sans-serif;font-weight:600;font-size:20px}
.footer ul{position:absolute;list-style:none;font-size:14.5px;line-height:30.5px}
.footer li{display:flex;align-items:center;gap:12px}
.fsoc{position:absolute;top:4530px;width:30px;height:30px;border-radius:50%;background:#fff;border:3px solid var(--green)}
.fcontact{position:absolute;display:flex;align-items:center;gap:16px;font-size:14.5px;line-height:25px}
.fcontact .ic{width:36px;height:36px;border-radius:50%;background:var(--green);display:flex;align-items:center;justify-content:center;flex:none}
.footer .rule{position:absolute;left:99px;top:339px;width:1002px;height:1px;background:#666}
.footer .copy{position:absolute;left:0;top:365px;width:1200px;text-align:center;font-size:14px}
</style>
</head>
<body>

<!-- header -->
<div class="abs brand" style="left:112px;top:30px;font-size:22px"><span class="dot"></span>Tidy paddock Services</div>
<div class="abs topbar">
  <div class="item" style="left:105px"><span class="ico-circle"><svg width="14" height="14" viewBox="0 0 24 24"><path fill="#5f9a13" d="M6.6 10.8a15.1 15.1 0 0 0 6.6 6.6l2.2-2.2a1 1 0 0 1 1-.25 11.4 11.4 0 0 0 3.6.57 1 1 0 0 1 1 1V20a1 1 0 0 1-1 1A17 17 0 0 1 3 4a1 1 0 0 1 1-1h3.5a1 1 0 0 1 1 1c0 1.25.2 2.45.57 3.6a1 1 0 0 1-.25 1z"/></svg></span>+1 555 0142 7788</div>
  <div class="item" style="left:308px"><span class="ico-circle"><svg width="14" height="14" viewBox="0 0 24 24"><path fill="#5f9a13" d="M2 5h20v14H2z"/><path d="M2 5l10 8 10-8" stroke="#fff" stroke-width="2" fill="none"/></svg></span>hello@tidypaddockservices.com</div>
  <span class="social" style="left:596px"></span>
  <span class="social" style="left:638px"></span>
  <span class="social" style="left:680px"></span>
  <span class="social" style="left:722px"></span>
</div>
<nav class="abs nav">
  <a class="active" style="left:539px">Home</a>
  <a style="left:641px">About Us</a>
  <a style="left:768px">Services</a>
  <a style="left:886px">Gallery</a>
  <a style="left:998px">Contact Us</a>
</nav>

<!-- hero -->
<section class="abs hero" role="img" aria-label="Smiling gardener tending vegetables in a raised garden bed">
  <h1>Do what you do best,<br>we'll do the rest.</h1>
  <p>Ut enim ad minim veniam, quis nostrud exercitation ullamco laboris nisi ut aliquip ex ea commodo consequat</p>
  <span class="btn">Get Started</span>
  <span class="arrow-c" style="left:41px;top:249px"><svg width="10" height="10" viewBox="0 0 10 10"><path d="M6.5 1L2.5 5l4 4" stroke="#fff" stroke-width="1.5" fill="none"/></svg></span>
  <span class="arrow-c" style="left:1128px;top:249px"><svg width="10" height="10" viewBox="0 0 10 10"><path d="M3.5 1l4 4-4 4" stroke="#fff" stroke-width="1.5" fill="none"/></svg></span>
</section>
<svg class="abs" style="left:0;top:580px" width="1200" height="130" viewBox="0 0 1200 130">
  <path d="M0 34 C250 100 550 118 820 100 C980 88 1100 60 1200 30 L1200 130 L0 130Z" fill="#fff"/>
  <path d="M390 120 C700 118 1000 70 1200 12 L1200 40 C1000 90 700 126 390 120Z" fill="#111"/>
  <path d="M470 104 C760 104 1000 55 1200 0 L1200 20 C1000 75 760 110 470 104Z" fill="#6aa817"/>
</svg>

<!-- why choose us -->
<div class="title" style="top:826px">
  <div class="l1"><span class="g">WHY</span> CHOOSE</div>
  <div class="l2"><i></i>US<i></i></div>
</div>
<p class="abs why-text">Lorem ipsum dolor sit amet, consectetur adipiscing elit, sed do eiusmod tempor incididunt ut labore et dolore magna aliqua. Ut enim ad minim veniam, quis nostrud exercitation ullamco laboris nisi ut aliquip ex ea commodo consequat.</p>
<div class="feature" style="left:150px">
  <svg width="56" height="56" viewBox="0 0 56 56" fill="none" stroke="#222" stroke-width="2"><rect x="6" y="14" width="28" height="36"/><rect x="34" y="26" width="16" height="24"/><path d="M12 22h6M22 22h6M12 30h6M22 30h6M12 38h6M22 38h6M18 50v-6h6v6M12 14V6h8v8"/></svg>
  <span>Lorem ipsum</span>
</div>
<div class="feature" style="left:382px">
  <svg width="56" height="56" viewBox="0 0 56 56" fill="none" stroke="#222" stroke-width="2"><rect x="10" y="6" width="30" height="40" transform="rotate(-8 25 26)"/><path d="M16 16h16M16 24h16M16 32h10"/><circle cx="38" cy="42" r="9"/><circle cx="38" cy="42" r="4"/></svg>
  <span>Lorem ipsum</span>
</div>
<div class="feature" style="left:613px">
  <svg width="56" height="56" viewBox="0 0 56 56" fill="none" stroke="#222" stroke-width="2"><circle cx="28" cy="28" r="24"/><circle cx="28" cy="18" r="4"/><path d="M21 30a7 7 0 0 1 14 0"/><circle cx="18" cy="34" r="4"/><path d="M11 46a7 7 0 0 1 14 0"/><circle cx="38" cy="34" r="4"/><path d="M31 46a7 7 0 0 1 14 0"/></svg>
  <span>Lorem ipsum</span>
</div>
<div class="feature" style="left:845px">
  <svg width="56" height="56" viewBox="0 0 56 56" fill="none" stroke="#222" stroke-width="2"><rect x="24" y="4" width="20" height="22"/><path d="M28 10h4M36 10h4M28 16h4M36 16h4M14 26V14h10"/><circle cx="12" cy="38" r="5"/><path d="M4 52a8 8 0 0 1 16 0"/><circle cx="44" cy="38" r="5"/><path d="M36 52a8 8 0 0 1 16 0M22 42h10M28 38l4 4-4 4"/></svg>
  <span>Lorem ipsum</span>
</div>

<!-- about -->
<section class="abs about">
  <h2>ABOUT US<i></i></h2>
  <p>Sed ut perspiciatis unde omnis iste natus error sit voluptatem accusantium doloremque laudantium, totam rem aperiam, eaque ipsa quae ab illo inventore veritatis et quasi architecto beatae vitae dicta sunt explicabo. Nemo enim ipsam voluptatem quia voluptas sit aspernatur aut odit aut fugit, sed quia consequuntur magni dolores eos qui ratione voluptatem sequi nesciunt. Neque porro quisquam est, qui dolorem ipsum quia dolor sit amet, consectetur, adipisci velit, dolore magnam aliquam quaerat voluptatem.</p>
  <span class="btn">Read More</span>
</section>
<div class="abs about-photo" role="img" aria-label="Timber deck with outdoor dining furniture beside a house and pine trees"></div>

<!-- services -->
<div class="abs brand svc-brand"><span class="dot"></span>Tidy paddock Services</div>
<span class="svc-arrow" style="left:48px"><svg width="10" height="10" viewBox="0 0 10 10"><path d="M6.5 1L2.5 5l4 4" stroke="#777" stroke-width="1.5" fill="none"/></svg></span>
<span class="svc-arrow" style="left:1127px"><svg width="10" height="10" viewBox="0 0 10 10"><path d="M3.5 1l4 4-4 4" stroke="#777" stroke-width="1.5" fill="none"/></svg></span>
<article class="card" style="left:99px">
  <div class="pic" role="img" aria-label="Farmer in a wheat field holding green shoots" style="background:linear-gradient(180deg,#e6e6e6 0%,#a7b86a 55%,#6c8f2c 100%)"></div>
  <h3>Stock Work</h3>
</article>
<article class="card featured" style="left:441px">
  <div class="pic" role="img" aria-label="White farmhouse behind a white picket fence" style="height:247px;background:linear-gradient(180deg,#9cc0e6 0%,#e8ecef 55%,#7aa352 100%)"></div>
  <h3>Fencing</h3>
  <ul>
    <li>Stock fencing</li>
    <li>Post &amp; rail</li>
    <li>Stock yards repair</li>
    <li>Electric fencing install &amp; repairs</li>
  </ul>
</article>
<article class="card" style="left:784px">
  <div class="pic" role="img" aria-label="Gloved hand spraying leafy green plants" style="background:linear-gradient(180deg,#cfe3e0 0%,#4f8b33 55%,#2e5d1c 100%)"></div>
  <h3>Spraying</h3>
</article>

<!-- gallery -->
<section class="abs gallery">
  <h2>GALLERY<i></i></h2>
</section>
<div class="tile" role="img" aria-label="Timber retaining steps set into a grassy slope" style="left:112px;top:2966px;width:434px;height:297px;background:linear-gradient(160deg,#6d7a4a,#8e8c7c 50%,#4e5e2e)"></div>
<div class="tile" role="img" aria-label="Workers building a wooden fence" style="left:568px;top:2966px;width:249px;height:297px;background:linear-gradient(90deg,#8a6a48,#a9876a 45%,#3d4a5a)"></div>
<div class="tile" role="img" aria-label="Smiling woman in a sun hat holding a tray of burgers" style="left:839px;top:2966px;width:251px;height:297px;background:linear-gradient(180deg,#8fa86a,#4a6a8a 60%,#a77a4a)"></div>
<div class="tile" role="img" aria-label="Garden trowel in soil beside a seedling" style="left:112px;top:3288px;width:249px;height:297px;background:linear-gradient(180deg,#a9c98a,#5a3a22 60%,#3a2414)"></div>
<div class="tile" role="img" aria-label="Old red barn among trees" style="left:381px;top:3288px;width:251px;height:297px;background:linear-gradient(180deg,#9ab8c8,#4a6a2a 45%,#8a4a32 65%,#6a8a3a)"></div>
<div class="tile" role="img" aria-label="Gloved hands trimming a hedge with shears" style="left:654px;top:3288px;width:436px;height:297px;background:linear-gradient(120deg,#3e6a22,#6a9a32 50%,#c9d4bf)"></div>

<!-- contact -->
<div class="title" style="top:3817px">
  <div class="l1" style="color:var(--green)">CONTACT</div>
  <div class="l2"><i></i>US<i></i></div>
</div>
<div class="field" style="left:181px;top:3935px;width:411px">Name</div>
<div class="field" style="left:606px;top:3935px;width:411px">Email</div>
<div class="field" style="left:181px;top:3997px;width:411px">Phone Number</div>
<div class="field" style="left:606px;top:3997px;width:411px">Subject</div>
<div class="field" style="left:181px;top:4060px;width:836px;height:84px">Message</div>
<span class="abs btn contact-submit">Submit</span>

<!-- footer -->
<footer class="abs footer">
  <div class="abs brand" style="left:92px;top:118px;font-size:23px"><span class="dot"></span>Tidy paddock Services</div>
  <h4 style="left:449px">Quick Links</h4>
  <ul style="left:449px;top:116px">
    <li><svg width="12" height="12" viewBox="0 0 12 12"><path d="M1 6h9M6 2l4 4-4 4" stroke="#fff" stroke-width="2" fill="none"/></svg>Home</li>
    <li><svg width="12" height="12" viewBox="0 0 12 12"><path d="M1 6h9M6 2l4 4-4 4" stroke="#fff" stroke-width="2" fill="none"/></svg>About Us</li>
    <li><svg width="12" height="12" viewBox="0 0 12 12"><path d="M1 6h9M6 2l4 4-4 4" stroke="#fff" stroke-width="2" fill="none"/></svg>Services</li>
    <li><svg width="12" height="12" viewBox="0 0 12 12"><path d="M1 6h9M6 2l4 4-4 4" stroke="#fff" stroke-width="2" fill="none"/></svg>Gallery</li>
    <li><svg width="12" height="12" viewBox="0 0 12 12"><path d="M1 6h9M6 2l4 4-4 4" stroke="#fff" stroke-width="2" fill="none"/></svg>Contact Us</li>
  </ul>
  <h4 style="left:647px">Other Links</h4>
  <ul style="left:647px;top:114px">
    <li><svg width="12" height="12" viewBox="0 0 12 12"><path d="M1 6h9M6 2l4 4-4 4" stroke="#fff" stroke-width="2" fill="none"/></svg>FAQ</li>
    <li><svg width="12" height="12" viewBox="0 0 12 12"><path d="M1 6h9M6 2l4 4-4 4" stroke="#fff" stroke-width="2" fill="none"/></svg>Terms of Use</li>
    <li><svg width="12" height="12" viewBox="0 0 12 12"><path d="M1 6h9M6 2l4 4-4 4" stroke="#fff" stroke-width="2" fill="none"/></svg>Privacy Policy</li>
    <li><svg width="12" height="12" viewBox="0 0 12 12"><path d="M1 6h9M6 2l4 4-4 4" stroke="#fff" stroke-width="2" fill="none"/></svg>Support Links</li>
    <li><svg width="12" height="12" viewBox="0 0 12 12"><path d="M1 6h9M6 2l4 4-4 4" stroke="#fff" stroke-width="2" fill="none"/></svg>Conditions</li>
  </ul>
  <h4 style="left:846px">Contact Us</h4>
  <div class="fcontact" style="left:846px;top:122px"><span class="ic"><svg width="14" height="16" viewBox="0 0 14 18"><path d="M7 0a7 7 0 0 1 7 7c0 5-7 11-7 11S0 12 0 7a7 7 0 0 1 7-7z" fill="#fff"/><circle cx="7" cy="7" r="2.5" fill="#5f9a13"/></svg></span><span>Tidy paddock Services,<br>United State.</span></div>
  <div class="fcontact" style="left:846px;top:187px"><span class="ic"><svg width="16" height="12" viewBox="0 0 16 12"><rect width="16" height="12" fill="#fff"/><path d="M0 0l8 6 8-6" stroke="#5f9a13" stroke-width="1.5" fill="none"/></svg></span><span>hello@tidypaddockservices.com</span></div>
  <div class="fcontact" style="left:846px;top:247px"><span class="ic"><svg width="15" height="15" viewBox="0 0 24 24"><path fill="#fff" d="M6.6 10.8a15.1 15.1 0 0 0 6.6 6.6l2.2-2.2a1 1 0 0 1 1-.25 11.4 11.4 0 0 0 3.6.57 1 1 0 0 1 1 1V20a1 1 0 0 1-1 1A17 17 0 0 1 3 4a1 1 0 0 1 1-1h3.5a1 1 0 0 1 1 1c0 1.25.2 2.45.57 3.6a1 1 0 0 1-.25 1z"/></svg></span><span>+1 555 0142 7788</span></div>
  <div class="rule"></div>
  <p class="copy">Copyrights@2024.Tidy paddock Services.All Rights Reserved</p>
</footer>
<span class="fsoc" style="left:141px"></span>
<span class="fsoc" style="left:183px"></span>
<span class="fsoc" style="left:227px"></span>
<span class="fsoc" style="left:269px"></span>

</body>
</html>
```